Telecommunications Company needs a business card design

We are looking for a sleek, professional and modern business card design based off our new logo. Will look at both light and dark options. On some designs please provide a small space for a QR code

Target Market(s)

B2B clients in Australia

Contact Information for Business Card

Name, Position, Brisbane (head) office, Phone number, email address, QR code (link to our website qlinetelecom.com.au

Colors
0054AA
0677BA
7BADD7
CADEEF
E8F1F8
0094D4
00A9DD
6FCCEA
C7EBF8
E9F6FB
00AB8E
00BBA5
67D7C9
C6EFE9
E9F9F6

```html
<!DOCTYPE html>
<html lang="en">
<head>
<meta charset="utf-8">
<title>Qline Telecom — Business Card</title>
<link href="https://fonts.googleapis.com/css2?family=Arimo:wght@400;700&display=swap" rel="stylesheet">
<style>
  :root {
    --backdrop: #9b9b9b;
    --card-light: #ffffff;
    --card-dark: #2c2b2c;
    --brand-blue: #0677BA;
    --brand-deep: #0054AA;
    --brand-teal: #14a5ad;
    --name-teal: #179aa1;
    --steel: #8a939c;
    --ink: #4a4a4a;
    --white: #ffffff;
  }
  html, body {
    margin: 0;
    padding: 0;
    width: 1133px;
    height: 1200px;
    overflow: hidden;
    background: var(--backdrop);
    font-family: "Arimo", Arial, sans-serif;
  }
  .canvas { position: relative; width: 1133px; height: 1200px; }
  .card { position: absolute; width: 706px; height: 402px; overflow: hidden; }
  .card--front { left: 209px; top: 148px; background: var(--card-light); }
  .card--back { left: 216px; top: 644px; background: var(--card-dark); }

  .identity { position: absolute; right: 405px; top: 174px; text-align: right; }
  .identity__name { margin: 0; font-size: 24px; font-weight: 700; color: var(--name-teal); line-height: 28px; }
  .identity__role { margin: 0; font-size: 16px; font-weight: 700; color: var(--steel); line-height: 20px; }

  .divider { position: absolute; left: 311px; top: 148px; width: 1.5px; height: 105px; background: var(--ink); }

  .contact { position: absolute; left: 330px; top: 150px; font-size: 16px; color: var(--ink); line-height: 20px; }
  .contact p { margin: 0; }
  .contact__gap { height: 8px; }

  .band { position: absolute; left: 0; top: 340px; height: 31px; width: 706px; }
  .band__stripe {
    position: absolute; left: 0; top: 0; height: 31px; width: 500px;
    background: linear-gradient(90deg, var(--brand-blue) 0%, var(--brand-teal) 45%, var(--brand-blue) 100%);
  }
  .band__web {
    position: absolute; left: 116px; top: 7px; font-size: 15px; letter-spacing: 3.3px;
    color: var(--white); line-height: 17px;
  }
  .band__brand {
    position: absolute; left: 506px; top: 6px; font-size: 16px; font-weight: 700;
    color: var(--brand-blue); line-height: 19px; white-space: nowrap;
  }
  .band__steel { position: absolute; left: 624px; top: 0; height: 31px; width: 82px; background: var(--steel); }

  .wordmark {
    position: absolute; left: 0; right: 0; top: 168px; text-align: center;
    font-size: 56px; font-weight: 700; color: var(--steel); line-height: 64px;
  }
</style>
</head>
<body>
<div class="canvas">
  <section class="card card--front" aria-label="Business card front">
    <div class="identity">
      <p class="identity__name">Mark Henley</p>
      <p class="identity__role">Managing Director</p>
    </div>
    <div class="divider"></div>
    <div class="contact">
      <p>Brisbane (head) office</p>
      <p>218 Carrow Street</p>
      <p>Kelvin Grove</p>
      <div class="contact__gap"></div>
      <p>1300 555 214</p>
      <p>info@qlinetelecom.com.au</p>
    </div>
    <div class="band">
      <div class="band__stripe"></div>
      <span class="band__web">www.qlinetelecom.com.au</span>
      <span class="band__brand">Qline Telecom</span>
      <div class="band__steel"></div>
    </div>
  </section>

  <section class="card card--back" aria-label="Business card back">
    <div class="wordmark">Qline Telecom</div>
  </section>
</div>
</body>
</html>
```